I need a business card design for a new business based in South West Australia.
I specialize in residential window cleaning & general handyman maintenance.

Dale Marsh - 412 SILVER HAWK DETAILING
- Window Cleaning
- House Maintenance

```html
<!DOCTYPE html>
<html lang="en">
<head>
<meta charset="utf-8">
<title>Silver Hawk Detailing – Business Card</title>
<link href="https://fonts.googleapis.com/css2?family=Lato:wght@400;700;900&display=swap" rel="stylesheet">
<style>
  :root {
    --stage-top: #2b2b2b;
    --stage-bottom: #050505;
    --card-white: #f3f3f3;
    --brand-blue: #0b4ea2;
    --brand-blue-light: #1466c4;
    --brand-blue-deep: #0a4a9c;
    --brand-orange: #f26a10;
    --ink: #333333;
    --white: #ffffff;
  }
  * { margin: 0; padding: 0; box-sizing: border-box; }
  html, body { width: 1200px; height: 900px; overflow: hidden; }
  body {
    position: relative;
    background: linear-gradient(180deg, var(--stage-top) 0%, #1a1a1a 55%, var(--stage-bottom) 100%);
    font-family: "Lato", Arial, sans-serif;
  }
  .card {
    position: absolute;
    top: 184px;
    height: 490px;
    border-radius: 14px;
    overflow: hidden;
    text-align: center;
  }
  .card--front { left: 299px; width: 301px; background: var(--card-white); }
  .card--back {
    left: 645px; width: 305px;
    background: linear-gradient(160deg, var(--brand-blue-light) 0%, var(--brand-blue-deep) 100%);
  }
  .wordmark {
    position: absolute; left: 0; right: 0;
    font-weight: 900; letter-spacing: -0.3px; line-height: 1;
  }
  .card--front .wordmark { top: 122px; font-size: 25px; color: var(--brand-blue); }
  .card--back .wordmark { top: 419px; font-size: 25px; color: var(--white); }
  .tagline {
    position: absolute; left: 0; right: 0;
    font-weight: 700; font-size: 10.5px; letter-spacing: 0.4px; line-height: 1;
  }
  .card--front .tagline { top: 151px; color: var(--brand-orange); }
  .card--back .tagline { top: 447px; color: var(--white); }
  .mark-dot {
    position: absolute; left: 128px; top: 40px;
    width: 46px; height: 46px; border-radius: 50%;
    background: var(--brand-blue);
  }
  .person { position: absolute; top: 246px; left: 0; right: 0; }
  .person__name { font-size: 24px; font-weight: 400; color: var(--brand-blue); letter-spacing: 0.3px; line-height: 1.1; }
  .person__role { font-size: 14.5px; color: var(--ink); margin-top: 4px; }
  .contact { position: absolute; top: 311px; left: 0; right: 0; font-size: 14.5px; color: var(--ink); line-height: 20px; }
  .contact__line { display: flex; justify-content: center; align-items: center; gap: 6px; }
  .contact__icon { width: 11px; height: 11px; fill: var(--brand-blue); }
  .address { position: absolute; top: 420px; left: 0; right: 0; font-size: 14.5px; color: var(--ink); line-height: 16px; }
  .back-decoration {
    position: absolute; left: 0; top: 0; width: 100%; height: 400px;
    background: radial-gradient(ellipse at 40% 45%, rgba(40,120,210,0.45) 0%, rgba(20,90,180,0.15) 55%, rgba(10,74,156,0) 80%);
  }
</style>
</head>
<body>
  <section class="card card--front" aria-label="Business card front">
    <div class="mark-dot"></div>
    <div class="wordmark">SILVER HAWK DETAILING</div>
    <div class="tagline">WINDOW CLEANING &amp; HOUSE MAINTENANCE</div>

    <div class="person">
      <div class="person__name">DALE MARSH</div>
      <div class="person__role">Managing Director</div>
    </div>

    <div class="contact">
      <div class="contact__line">
        <svg class="contact__icon" viewBox="0 0 12 12" aria-hidden="true"><path d="M1 4c0-1.5 2-2.5 5-2.5S11 2.5 11 4v1H8.5V3.8h-5V5H1zM3 6h6l1.5 4.5h-9z"/></svg>
        <span>08 9721 4630</span>
      </div>
      <div class="contact__line">
        <svg class="contact__icon" viewBox="0 0 12 12" aria-hidden="true"><path d="M1 3h10v6H1z M1 3l5 3.5L11 3" stroke="#f3f3f3" stroke-width="0.8"/></svg>
        <span>dale@silverhawkwa.au</span>
      </div>
    </div>

    <div class="address">
      <div>17 Karri Ridge Road</div>
      <div>Bunbury WA, 6230</div>
    </div>
  </section>

  <section class="card card--back" aria-label="Business card back">
    <div class="back-decoration" role="img" aria-label="Large faint brand window symbol as background decoration"></div>
    <div class="wordmark">SILVER HAWK DETAILING</div>
    <div class="tagline">WINDOW CLEANING &amp; HOUSE MAINTENANCE</div>
  </section>
</body>
</html>
```